Business Card for: Bramwell Financial Advisory Services Inc.

provide strategic financial advisory services to companies in the areas of corporate finance, mergers and acquisitions, executive coaching and strategic planning

Target Market(s)

Companies, banks, accountants, lawyers

Industry/Entity Type

High end business consulting in corporate finance, mergers and acquisitions, consulting

Contact Information for Business Card

Name of company, Name: xxxxxx xxxxxx , CEO, - phone number: 1-xxx-xxx-xxxx, - email address,

Requirements
Must have
• Must be professional and simple.
Nice to have
• simple, straight graphics, must give the impression that we are trustworthy, professional, competent
Should not have
• loud colors, loud design features

```html
<!DOCTYPE html>
<html lang="en">
<head>
<meta charset="utf-8">
<title>Bramwell Financial Advisory Services Inc. — Business Card</title>
<link rel="stylesheet" href="https://fonts.googleapis.com/css2?family=Quicksand:wght@500;700&display=swap">
<style>
  :root {
    --bg: #2b2b2b;
    --card-dark: #1f1f20;
    --card-dark-mark: #343436;
    --card-light: #ffffff;
    --ink: #1d1d1f;
    --ink-soft: #444448;
    --divider: #b9b9bd;
    --blue-deep: #0a79bd;
    --blue-bright: #2cb5dc;
    --icon-bg: #3fbde3;
  }
  * { box-sizing: border-box; margin: 0; padding: 0; }
  html, body { width: 1200px; height: 689px; overflow: hidden; }
  body {
    background: var(--bg);
    font-family: "Quicksand", sans-serif;
    position: relative;
  }
  .card {
    position: absolute;
    top: 196px;
    width: 520px;
    height: 297px;
    border-radius: 22px;
    overflow: hidden;
  }
  .card--back { left: 50px; background: var(--card-dark); }
  .card--front { left: 630px; background: var(--card-light); }

  /* Back side: company name as tone-on-tone mark */
  .back-brand {
    position: absolute;
    inset: 0;
    display: flex;
    align-items: center;
    justify-content: center;
    gap: 18px;
    color: var(--card-dark-mark);
    font-weight: 700;
  }
  .back-brand__dot {
    width: 54px; height: 54px; border-radius: 50%;
    background: var(--card-dark-mark);
  }
  .back-brand__name { font-size: 50px; line-height: 1; }
  .back-brand__sub { font-size: 17px; margin-top: 8px; }

  /* Front side */
  .front-brand {
    position: absolute;
    left: 36px; top: 92px;
    width: 230px;
    color: var(--ink);
    font-weight: 700;
  }
  .front-brand__dot {
    width: 40px; height: 40px; border-radius: 50%;
    background: var(--blue-bright);
    margin-bottom: 12px;
  }
  .front-brand__name { font-size: 38px; line-height: 1; }
  .front-brand__sub { font-size: 13px; margin-top: 6px; line-height: 1.3; }

  .divider {
    position: absolute;
    left: 282px; top: 60px;
    width: 1px; height: 150px;
    background: linear-gradient(var(--card-light), var(--divider) 30%, var(--divider) 70%, var(--card-light));
  }

  .contact {
    position: absolute;
    left: 304px; top: 66px;
    color: var(--ink);
  }
  .contact__name { font-size: 21px; font-weight: 700; line-height: 1.1; }
  .contact__title { font-size: 13px; font-weight: 500; color: var(--ink-soft); margin-bottom: 16px; }
  .contact__list { list-style: none; }
  .contact__item {
    display: flex; align-items: center; gap: 8px;
    font-size: 11.5px; font-weight: 500; color: var(--ink-soft);
    margin-bottom: 7px;
  }
  .contact__icon {
    width: 17px; height: 17px; border-radius: 3px;
    background: var(--icon-bg);
    display: flex; align-items: center; justify-content: center;
    flex: none;
  }
  .contact__item:nth-child(3) .contact__icon { background: var(--blue-deep); }

  .band {
    position: absolute;
    left: 0; bottom: 0;
    width: 520px; height: 70px;
  }
</style>
</head>
<body>

  <section class="card card--back" aria-label="Card back">
    <div class="back-brand">
      <div class="back-brand__dot"></div>
      <div>
        <div class="back-brand__name">Bramwell</div>
        <div class="back-brand__sub">Financial Advisory Services Inc.</div>
      </div>
    </div>
  </section>

  <section class="card card--front" aria-label="Card front">
    <div class="front-brand">
      <div class="front-brand__dot"></div>
      <div class="front-brand__name">Bramwell</div>
      <div class="front-brand__sub">Financial Advisory Services Inc.</div>
    </div>

    <div class="divider"></div>

    <div class="contact">
      <div class="contact__name">Everett Langley</div>
      <div class="contact__title">Managing Director</div>
      <ul class="contact__list">
        <li class="contact__item">
          <span class="contact__icon">
            <svg width="11" height="11" viewBox="0 0 24 24"><path fill="#fff" d="M6.6 10.8a15 15 0 0 0 6.6 6.6l2.2-2.2c.3-.3.7-.4 1-.2 1.1.4 2.3.6 3.6.6.6 0 1 .4 1 1V20c0 .6-.4 1-1 1A17 17 0 0 1 3 4c0-.6.4-1 1-1h3.5c.6 0 1 .4 1 1 0 1.3.2 2.5.6 3.6.1.3 0 .7-.2 1z"/></svg>
          </span>044-555 010 277
        </li>
        <li class="contact__item">
          <span class="contact__icon">
            <svg width="11" height="11" viewBox="0 0 24 24"><rect x="2" y="5" width="20" height="14" rx="1.5" fill="none" stroke="#fff" stroke-width="2"/><path d="M3 6l9 7 9-7" fill="none" stroke="#fff" stroke-width="2"/></svg>
          </span>info@bramwelladvisory.com
        </li>
        <li class="contact__item">
          <span class="contact__icon">
            <svg width="11" height="11" viewBox="0 0 24 24" fill="none" stroke="#fff" stroke-width="2"><circle cx="12" cy="12" r="9"/><path d="M3 12h18M12 3c3 3 3 15 0 18M12 3c-3 3-3 15 0 18"/></svg>
          </span>www.bramwelladvisory.com
        </li>
      </ul>
    </div>

    <svg class="band" viewBox="0 0 520 70" preserveAspectRatio="none" aria-hidden="true">
      <defs>
        <linearGradient id="band-fill" x1="0" x2="1" y1="0" y2="0">
          <stop offset="0" stop-color="var(--blue-deep)"/>
          <stop offset="1" stop-color="var(--blue-bright)"/>
        </linearGradient>
      </defs>
      <path d="M0 50 L380 46 Q470 44 520 8 L520 70 L0 70 Z" fill="url(#band-fill)"/>
    </svg>
  </section>

</body>
</html>
```